Business card design needed

I am a local business in the Blue Mountains area of Sydney. I am a sole trader and the business has been operating 7 months. To date the business has been built on referrals only and all my clinets for both home & commercial services are themselves business owners. I specialise in Home and Office cleaning and small business cleaning for example cafes, restuarants, health clinics.
I would like a clean looking design( maybe a white background). If its possible(not madatory) to incorporate a duster, or mop & bucket into the design or roof tops to communicate business premises that would be great. I would like my clients to know what the business is from the card. My uniform is navy with red/pink logo on .Attatched is the unifrom logo but it is not critical to match the font for the business card.
please put my name on contact details; Marla Quenby, Business owner.
Updates
Thank you very much to all the designers and their work efforts to submit a design for Tidal Fern Domestic Services. I have made a decision to accept the deign that Kobel Design of the United States submitted. Again Many thanks. Marla
Target Market(s)
business owners, generally women between 35-55
Industry/Entity Type
Small Business
Contact Information for Business Card
Tidal Fern Domestic Services,
specialist in Home & Small business cleaning
Kelmora Vale
tel: 0412559074 0412fernly
Logo Text
Tidal Fern Domestic Servies
Logo styles of interest
Emblem Logo
Abstract Logo
Wordmark Logo
Look and feel
Each slider illustrates characteristics of the customer's brand and the style your logo design should communicate.

```html
<!DOCTYPE html>
<html lang="en">
<head>
<meta charset="utf-8">
<title>Tidal Fern Domestic Services – Business Card</title>
<link rel="stylesheet" href="https://fonts.googleapis.com/css2?family=Alegreya+Sans:wght@500;700;800&display=swap">
<style>
  :root {
    --navy: #0b1f63;
    --sky: #a9cdf5;
    --accent: #e3161b;
    --paper: #ffffff;
  }
  * { margin: 0; padding: 0; box-sizing: border-box; }
  html, body {
    width: 1200px;
    height: 1000px;
    overflow: hidden;
    background: var(--paper);
  }
  .card {
    position: relative;
    width: 1200px;
    height: 1000px;
    font-family: "Alegreya Sans", sans-serif;
    color: var(--navy);
  }
  .rule {
    position: absolute;
    left: 148px;
    width: 902px;
    height: 4px;
    background: var(--navy);
  }
  .rule--top { top: 231px; }
  .rule--bottom { top: 763px; }
  .side-bar {
    position: absolute;
    top: 272px;
    width: 4px;
    height: 454px;
    background: linear-gradient(to bottom, var(--navy), var(--sky) 50%, var(--navy));
  }
  .side-bar--left { left: 106px; }
  .side-bar--right { left: 1087px; }
  .brand-mark {
    position: absolute;
    left: 420px;
    top: 262px;
    width: 84px;
    height: 84px;
    border-radius: 50%;
    background: var(--accent);
  }
  .brand-name {
    position: absolute;
    left: 232px;
    top: 372px;
    font-weight: 700;
    font-size: 98px;
    line-height: 1;
    letter-spacing: 1px;
    color: var(--navy);
  }
  .brand-sub {
    position: absolute;
    left: 436px;
    top: 474px;
    font-weight: 700;
    font-size: 64px;
    line-height: 1;
    color: var(--navy);
  }
  .contact-list {
    position: absolute;
    left: 160px;
    top: 546px;
    list-style: none;
    font-weight: 700;
    font-size: 29px;
    line-height: 33px;
  }
  .contact-list li::before {
    content: "•";
    font-size: 22px;
    margin-right: 5px;
    vertical-align: 3px;
  }
  .tagline {
    position: absolute;
    left: 0;
    width: 1200px;
    top: 699px;
    text-align: center;
    font-weight: 700;
    font-size: 41px;
    line-height: 1;
  }
</style>
</head>
<body>
  <main class="card">
    <div class="rule rule--top"></div>
    <div class="side-bar side-bar--left"></div>
    <div class="side-bar side-bar--right"></div>

    <div class="brand-mark"></div>
    <div class="brand-name">TIDAL FERN</div>
    <div class="brand-sub">Domestic Services</div>

    <ul class="contact-list">
      <li>Marla Quenby, Business owner</li>
      <li>Kelmora Vale</li>
      <li>0412 559 074</li>
      <li>tidalfern@seamail.com</li>
    </ul>

    <p class="tagline">• specialist in home &amp; small business cleaning •</p>

    <div class="rule rule--bottom"></div>
  </main>
</body>
</html>
```